Diverse, up-scale salon needs eye-catching, unique business cards.

We are looking for a unique business card design for our stylist but that can also be multi functional and used for appointment reminder and referrals. I will need a design in a format that I can modify names and titles going forward. In the past we have had a dark background with the logo on one side, and stylist and contact information on the other but we are open to all ideas. I have included our mission statement as well as branded colors below. The statement doesn't need to go on the card, it's just a reference for target market. We need space for the stylists name, title, instagram handle and then the salons phone number, website and address. I am also open to adding a spot for a qr code linked to the stylist instagram or the salon booking link.

primary brand colors:
#333333 #233415 #36502a #93874a #000000
Mission statement:
Vessolin Hair Studio, a high-end salon located in the lively Downtown Farmington, Michigan, is committed to providing exceptional services in a welcoming and relaxed environment to meet the needs of our diverse clientele.
Our salon specializes in contemporary custom haircuts, coloring, extensions, and barbering and beard grooming services. Our team of skilled stylists is passionate and inventive in their hair styling techniques. At the heart of our salon are values centered on quality, innovation, creativity, and above all, comfort. These core values are evident in every appointment across our customizable array of services.
Our goal is to establish a benchmark for exceptional hair care for every human.
Website: www.vessolinhairstudio.example
instagram: @vessolinhairstudio
address: 41782 Pelham Crest Rd, Farmington MI
phone: 248-613-4087

Industry/Entity Type

Hair Salon

Contact Information for Business Card

Stylist name, title, phone, instagram, website, address, (optional qr code)

Requirements
Should not have
• Does not need mission statement on the card.

```html
<!DOCTYPE html>
<html lang="en">
<head>
<meta charset="utf-8">
<title>Vessolin Hair Studio – Stylist Business Card</title>
<link rel="stylesheet" href="https://fonts.googleapis.com/css2?family=Open+Sans:wght@400;600;700&display=swap">
<style>
  :root {
    --page-bg: #e9e6e1;
    --card-dark: #1b1b1b;
    --card-mid: #2e2e2e;
    --gold: #93874a;
    --gold-bright: #a8974f;
    --text-light: #c9c6c0;
    --text-soft: #b3afa7;
  }
  * { box-sizing: border-box; margin: 0; padding: 0; }
  html, body {
    width: 1200px;
    height: 1047px;
    overflow: hidden;
    background: var(--page-bg);
    font-family: "Open Sans", Arial, sans-serif;
  }
  .business-card {
    position: absolute;
    left: 100px;
    top: 250px;
    width: 1000px;
    height: 547px;
    border-radius: 24px;
    background: linear-gradient(100deg, var(--card-dark) 0%, var(--card-mid) 45%, var(--card-dark) 100%);
    overflow: hidden;
  }
  .name-marker {
    position: absolute;
    left: 0;
    top: 228px;
    width: 25px;
    height: 34px;
    background: var(--gold);
  }
  .stylist-details {
    position: absolute;
    left: 40px;
    top: 226px;
    color: var(--text-light);
  }
  .stylist-name {
    font-size: 32px;
    font-weight: 700;
    color: var(--gold-bright);
    letter-spacing: 0.5px;
    line-height: 40px;
  }
  .stylist-title {
    font-size: 21px;
    font-weight: 400;
    color: var(--text-soft);
    margin-top: 2px;
    line-height: 30px;
  }
  .salon-address {
    font-size: 22px;
    line-height: 30px;
    margin-top: 24px;
    font-style: normal;
    color: var(--text-soft);
  }
  .contact-list {
    list-style: none;
    margin-top: 22px;
  }
  .contact-item {
    display: flex;
    align-items: center;
    gap: 10px;
    font-size: 21px;
    line-height: 30.5px;
    color: var(--text-soft);
  }
  .contact-icon {
    width: 16px;
    height: 16px;
    flex: none;
    fill: none;
    stroke: var(--text-soft);
    stroke-width: 1.8;
  }
  .brand-block {
    position: absolute;
    left: 560px;
    top: 150px;
    width: 360px;
    display: flex;
    flex-direction: column;
    align-items: center;
    gap: 26px;
  }
  .brand-ring {
    width: 150px;
    height: 150px;
    border-radius: 50%;
    border: 5px solid var(--gold);
  }
  .brand-name {
    font-size: 34px;
    font-weight: 600;
    color: var(--gold);
    letter-spacing: 4px;
    text-transform: uppercase;
    text-align: center;
    line-height: 44px;
  }
</style>
</head>
<body>
  <main class="business-card">
    <div class="name-marker"></div>
    <section class="stylist-details">
      <h1 class="stylist-name">MARCUS DELANE</h1>
      <p class="stylist-title">Managing Director</p>
      <address class="salon-address">41782 Pelham Crest Rd,<br>Farmington MI</address>
      <ul class="contact-list">
        <li class="contact-item">
          <svg class="contact-icon" viewBox="0 0 16 16"><path d="M3 1.5h3l1 3.5-2 1.2a8 8 0 0 0 4.8 4.8l1.2-2 3.5 1v3c0 .6-.5 1.1-1.1 1.1A12.5 12.5 0 0 1 1.9 2.6C1.9 2 2.4 1.5 3 1.5z"/></svg>
          <span>248-613-4087</span>
        </li>
        <li class="contact-item">
          <svg class="contact-icon" viewBox="0 0 16 16"><rect x="1.5" y="3.5" width="13" height="9" rx="1"/><path d="M1.5 4l6.5 5 6.5-5"/></svg>
          <span>info@vessolinhairstudio.example</span>
        </li>
        <li class="contact-item">
          <svg class="contact-icon" viewBox="0 0 16 16"><circle cx="8" cy="8" r="5.5"/></svg>
          <span>@vessolinhairstudio</span>
        </li>
        <li class="contact-item">
          <svg class="contact-icon" viewBox="0 0 16 16"><circle cx="8" cy="8" r="6.5"/><path d="M1.5 8h13M8 1.5c2.2 2.4 2.2 10.6 0 13M8 1.5c-2.2 2.4-2.2 10.6 0 13"/></svg>
          <span>www.vessolinhairstudio.example</span>
        </li>
      </ul>
    </section>
    <section class="brand-block">
      <div class="brand-ring"></div>
      <p class="brand-name">Vessolin<br>Hair Studio</p>
    </section>
  </main>
</body>
</html>
```